Established coffee roaster needs a coffee bag and label design

We need a new coffee bag design! PLEASE SEE THE DOCUMENT UPLOADED FOR DETAILS; COFFEE PACKAGING PROJECT TASK!
Coffee bag template attached. We will also need a pre-printed sticker label for changing coffee information. 3 Sticker label designed for one core coffee bag design. THANK YOU!!!

Went on vacation/holiday

```html
<!DOCTYPE html>
<html lang="en">
<head>
<meta charset="utf-8">
<title>Fernhill Roasting Co. – Coffee Bag Dieline</title>
<link href="https://fonts.googleapis.com/css2?family=Montserrat:wght@400;500;600;700&family=Rozha+One&display=swap" rel="stylesheet">
<style>
  :root{
    --ink:#050608;
    --paper:#ffffff;
    --navy:#243650;
    --terracotta:#b85243;
    --bronze:#9e6d38;
    --peach:#f9d3a1;
    --blush:#e5d5cd;
    --board-top:#f1f1f1;
    --board-bottom:#dcdde0;
    --label-grey:#666;
  }
  *{box-sizing:border-box;margin:0;padding:0}
  html,body{width:1200px;height:721px;overflow:hidden}
  body{
    position:relative;
    background:linear-gradient(180deg,var(--board-top),var(--board-bottom));
    font-family:"Montserrat",sans-serif;
  }
  .option-mark{position:absolute;left:45px;top:38px;font-size:40px;font-weight:500;color:var(--label-grey)}
  .palette{position:absolute;top:55px;left:416px;display:flex;gap:17px}
  .palette span{width:39px;height:39px;border-radius:6px}

  .panel{position:absolute;top:186px;height:338px;border-radius:9px}
  .panel::after{content:"";position:absolute;inset:6px 11px 11px 11px;border:1px dashed rgba(249,211,161,.45);pointer-events:none}
  .panel--side{width:140px;background:var(--terracotta)}
  .panel--face{width:191px;background:var(--navy)}
  .side-left{left:271px}
  .front{left:412px}
  .side-right{left:604px}
  .back{left:746px}
  .base{left:412px;top:525px;height:141px}
  .base::after{inset:11px}

  .side-title{position:absolute;left:0;top:0;width:140px;height:338px}
  .side-title text{font-family:"Rozha One",serif;fill:var(--peach);font-size:27px}

  .brand{position:absolute;top:78px;width:100%;text-align:center}
  .brand-dot{width:14px;height:14px;border-radius:50%;background:var(--peach);margin:0 auto 12px}
  .brand-name{font-size:11px;font-weight:500;color:var(--peach);line-height:1}

  .sticker{position:absolute;left:27px;top:185px;width:138px;height:95px;background:var(--bronze)}
  .sticker-scallops{position:absolute;left:0;top:-4px;width:138px;height:8px}
  .sticker-card{position:absolute;left:7px;top:9px;width:123px;height:80px;background:var(--blush);padding:0 5px;color:var(--ink);text-align:center}
  .sticker-title{font-size:10.5px;font-weight:500;margin-top:4px;padding-bottom:4px;border-bottom:.8px solid var(--navy)}
  .sticker-row{display:flex;border-bottom:.8px solid var(--navy)}
  .sticker-row:last-child{border-bottom:none}
  .sticker-cell{flex:1;padding:2px 0 2.5px}
  .sticker-cell + .sticker-cell{border-left:.8px solid var(--navy)}
  .field-label{display:block;font-size:3.6px;color:var(--terracotta)}
  .field-value{display:block;font-size:5.4px;font-weight:500}

  .contact{position:absolute;top:294px;left:0;width:100%;text-align:center;color:var(--paper);font-size:6.3px;line-height:1.35}
  .contact::before,.contact::after{content:"";position:absolute;top:6px;width:17px;border-top:.8px solid var(--peach)}
  .contact::before{left:27px}
  .contact::after{right:27px}

  .back-intro{position:absolute;top:98px;left:30px;right:30px;text-align:center;color:var(--paper);font-size:6.4px;font-weight:600;line-height:1.2}
  .virtue-frame{position:absolute;left:30px;top:142px;width:130px;height:62px;border:.8px solid var(--peach);border-top:none}
  .virtue-frame::before,.virtue-frame::after{content:"";position:absolute;top:0;width:6px;border-top:.8px solid var(--peach)}
  .virtue-frame::before{left:0}
  .virtue-frame::after{right:0}
  .virtue-icons{position:absolute;left:12px;top:-8px;width:106px;height:15px;border-radius:8px;background:var(--peach)}
  .virtue-copy{position:absolute;top:22px;left:6px;right:6px;text-align:center;color:var(--peach);font-size:5.2px;line-height:1.22}
  .back-est{position:absolute;top:211px;width:100%;text-align:center;color:var(--peach);font-size:7px}
  .back-band{position:absolute;left:31px;top:276px;width:129px;height:16px;background:var(--peach);color:var(--navy);font-size:5.2px;font-weight:700;text-align:center;line-height:1.2;padding-top:2px}

  .recycle{position:absolute;left:58px;top:46px;display:flex;align-items:center;gap:5px}
  .recycle-icon{width:17px;height:17px}
  .recycle-note{color:var(--paper);font-size:4px;font-weight:500;line-height:1.2}
</style>
</head>
<body>
  <div class="option-mark">A</div>

  <div class="palette">
    <span style="background:var(--ink)"></span>
    <span style="background:var(--paper)"></span>
    <span style="background:var(--navy)"></span>
    <span style="background:var(--terracotta)"></span>
    <span style="background:var(--bronze)"></span>
    <span style="background:var(--peach)"></span>
    <span style="background:var(--blush)"></span>
  </div>

  <section class="panel panel--side side-left">
    <svg class="side-title" viewBox="0 0 140 338"><text transform="translate(84 311) rotate(-90)" textLength="283" lengthAdjust="spacingAndGlyphs">SINGLE ORIGIN COFFEE</text></svg>
  </section>

  <section class="panel panel--face front">
    <div class="brand">
      <div class="brand-dot"></div>
      <div class="brand-name">Fernhill Roasting Co.</div>
    </div>

    <div class="sticker">
      <svg class="sticker-scallops" viewBox="0 0 138 8">
        <path fill="var(--bronze)" d="M0 4 H138 V8 H0Z"/>
        <g fill="var(--navy)">
          <circle cx="12" cy="0" r="5"/><circle cx="31" cy="0" r="5"/><circle cx="50" cy="0" r="5"/>
          <circle cx="69" cy="0" r="5"/><circle cx="88" cy="0" r="5"/><circle cx="107" cy="0" r="5"/><circle cx="126" cy="0" r="5"/>
        </g>
      </svg>
      <div class="sticker-card">
        <div class="sticker-title">Ethiopia Reko</div>
        <div class="sticker-row">
          <div class="sticker-cell"><span class="field-label">Process</span><span class="field-value">Natural</span></div>
          <div class="sticker-cell"><span class="field-label">Roast</span><span class="field-value">Medium</span></div>
        </div>
        <div class="sticker-row">
          <div class="sticker-cell"><span class="field-label">Gratitude Flavor Profile 1</span><span class="field-value">Bright, Fruity, Floral</span></div>
        </div>
        <div class="sticker-row">
          <div class="sticker-cell"><span class="field-label">Best Before Date</span><span class="field-value">August, 15 2024</span></div>
          <div class="sticker-cell"><span class="field-label">Net Weight</span><span class="field-value">12 oz</span></div>
        </div>
      </div>
    </div>

    <div class="contact">www.fernhillroasting.com<br>@fernhillroasting</div>
  </section>

  <section class="panel panel--side side-right">
    <svg class="side-title" viewBox="0 0 140 338"><text transform="translate(84 311) rotate(-90)" textLength="283" lengthAdjust="spacingAndGlyphs">SINGLE ORIGIN COFFEE</text></svg>
  </section>

  <section class="panel panel--face back">
    <p class="back-intro">Fernhill Single Origin Coffee offers a pure, hand-crafted experience from farm to cup.</p>
    <div class="virtue-frame">
      <div class="virtue-icons" role="img" aria-label="Row of seven small value emblems"></div>
      <p class="virtue-copy">Our seven values, compassion, gratitude, honesty, humility, kindness, forgiveness, and patience are ideals that we strive for. Embrace a value and move forward with your daily life in a positive way!</p>
    </div>
    <p class="back-est">Established 2007, Cedar Falls, Maine</p>
    <div class="back-band">Fernhill Roasting Co.<br>Established 2007, Cedar Falls, Maine</div>
  </section>

  <section class="panel panel--face base">
    <div class="recycle">
      <svg class="recycle-icon" viewBox="0 0 20 20" aria-hidden="true">
        <g fill="none" stroke="var(--paper)" stroke-width="2.2">
          <path d="M10 3 L15 11"/><path d="M15 14 H5"/><path d="M3.5 11 L8 3.5"/>
        </g>
        <g fill="var(--paper)">
          <path d="M16.5 9 L16 13.5 L12 11.5Z"/><path d="M7 16.5 L3 14 L7 11.5Z"/><path d="M6 2.5 L10 1 L9.5 5.5Z"/>
        </g>
      </svg>
      <p class="recycle-note">Help protect all living<br>things, and please<br>recycle this bag afteruse</p>
    </div>
  </section>
</body>
</html>
```